CREATE A BUSINESS CARD FOR A BOAT CLEANING SERVICE

WE ARE STARTING A NEW BOAT CLEANING BUSINESS. WE DIVE UNDERWATER TO CLEAN BOAT HULLS, JETTIES, UNDERWATER STRUCTURES ETC. WE ARE LOOKING FOR AN UPPERMARKET MODERN LOGO AND BUSINESS CARD AS ALOT OF OUR TARGET MARKET WILL BE HIGH END. YOU HAVE TO DESIGN A BUSINESS CARD AND LOGO SEPERATELY .
THE BUSINESS CARD DIMESNION MUST BE STANDARD SIZE.
The standard dimensions of a printed business card are 3.5 x 2 inches

Target Market(s)

UNDERWATER SERVICED

Industry/Entity Type

Business

Contact Information for Business Card

HOLLAND UNDERWATER SERVICES

Font styles to use
Serif

Colors

Designer to choose colors to be used in the design.

Requirements
Must have
• HOLLAND
Nice to have
• dark
Should not have
• more than 3 colors

```html
<!DOCTYPE html>
<html lang="en">
<head>
<meta charset="utf-8">
<title>Holland Underwater Service – Business Cards</title>
<link rel="stylesheet" href="https://fonts.googleapis.com/css2?family=Montserrat:wght@400;500;600&family=Open+Sans:wght@400;600&display=swap">
<style>
  :root {
    --brand-blue: #0f4f82;
    --ink-gray: #8a8a8a;
    --band-gray: #8c8c8c;
    --paper: #ffffff;
    --backdrop: #e9e9e7;
  }
  * { box-sizing: border-box; margin: 0; padding: 0; }
  html, body {
    width: 1200px; height: 930px; overflow: hidden;
    background: var(--backdrop);
  }
  .sheet {
    position: relative; width: 1200px; height: 930px;
    display: flex; flex-direction: column; align-items: center; justify-content: center; gap: 60px;
  }
  .card {
    position: relative; width: 560px; height: 320px;
    border-radius: 16px; overflow: hidden;
    box-shadow: 0 6px 18px rgba(0,0,0,0.18);
  }
  .card--front { background: var(--brand-blue); }
  .card--back { background: var(--paper); }

  .wordmark { position: absolute; font-family: "Montserrat", sans-serif; white-space: nowrap; }
  .wordmark__name { display: block; font-weight: 500; }
  .wordmark__tagline { display: block; font-weight: 400; }

  .card--front .wordmark { left: 0; right: 0; top: 118px; text-align: center; color: var(--paper); }
  .card--front .wordmark__name { font-size: 40px; letter-spacing: 0.55em; padding-left: 0.55em; }
  .card--front .wordmark__tagline { font-size: 17px; letter-spacing: 0.28em; margin-top: 10px; padding-left: 0.28em; }

  .card--back .wordmark { left: 32px; top: 124px; width: 240px; }
  .card--back .wordmark__name { font-size: 25px; letter-spacing: 0.45em; color: var(--brand-blue); }
  .card--back .wordmark__tagline { font-size: 11.5px; letter-spacing: 0.24em; color: var(--ink-gray); margin-top: 8px; }

  .divider {
    position: absolute; left: 290px; top: 60px; width: 1px; height: 150px;
    background: var(--brand-blue);
  }
  .contact {
    position: absolute; left: 312px; top: 52px; width: 240px;
    font-family: "Open Sans", sans-serif; color: var(--ink-gray);
  }
  .contact__name {
    font-family: "Montserrat", sans-serif; font-weight: 600;
    font-size: 21px; color: var(--brand-blue); line-height: 1.1;
  }
  .contact__role { font-size: 12px; margin-bottom: 10px; }
  .contact__address { font-size: 12px; line-height: 1.4; margin-bottom: 8px; }
  .contact__line { display: flex; align-items: center; gap: 7px; font-size: 12px; line-height: 1.5; }
  .contact__line svg { width: 10px; height: 10px; flex: none; fill: var(--brand-blue); }
  .contact__web-domain { color: var(--brand-blue); }

  .partners {
    position: absolute; left: 330px; top: 214px;
    display: flex; align-items: center; gap: 18px;
  }
  .partners__badge { width: 30px; height: 30px; border-radius: 50%; background: var(--brand-blue); opacity: 0.75; }
  .partners__mark { display: flex; align-items: center; gap: 6px; }
  .partners__dot { width: 18px; height: 18px; border-radius: 50%; background: #1c1c1c; }
  .partners__name { font-family: "Montserrat", sans-serif; font-weight: 600; font-size: 15px; color: #1c1c1c; letter-spacing: 0.04em; }

  .bands { position: absolute; left: 0; top: 0; width: 560px; height: 320px; }
</style>
</head>
<body>
<main class="sheet">
  <section class="card card--front" aria-label="Card front">
    <div class="wordmark">
      <span class="wordmark__name">HOLLAND</span>
      <span class="wordmark__tagline">UNDERWATER SERVICE</span>
    </div>
  </section>

  <section class="card card--back" aria-label="Card back">
    <svg class="bands" viewBox="0 0 560 320" aria-hidden="true">
      <polygon points="0,268 372,268 360,302 0,302" fill="var(--band-gray)"/>
      <polygon points="390,256 560,256 560,282 380,282" fill="var(--brand-blue)"/>
    </svg>

    <div class="wordmark">
      <span class="wordmark__name">HOLLAND</span>
      <span class="wordmark__tagline">UNDERWATER SERVICE</span>
    </div>

    <div class="divider"></div>

    <div class="contact">
      <p class="contact__name">DANIEL REEVES</p>
      <p class="contact__role">President</p>
      <p class="contact__address">310, 418 - 9th Ave, SW<br>Calgary, AB T2P 1K4</p>
      <p class="contact__line">
        <svg viewBox="0 0 10 10"><path d="M2 0.5 L3.8 2.6 L2.9 3.8 Q4 6 6.2 7.1 L7.4 6.2 L9.5 8 L8.3 9.5 Q4.5 9.5 0.5 1.7 Z"/></svg>
        (410) 555-0192
      </p>
      <p class="contact__line">
        <svg viewBox="0 0 10 10"><path d="M0.5 2 H9.5 V8 H0.5 Z M1.5 3 V7 H8.5 V3 L5 5.6 Z" fill-rule="evenodd"/></svg>
        info@hollandunderwater.com
      </p>
      <p class="contact__line">
        <svg viewBox="0 0 10 10"><circle cx="5" cy="5" r="4.5"/></svg>
        <span>www.<span class="contact__web-domain">hollandunderwater</span>.com</span>
      </p>
    </div>

    <div class="partners">
      <div class="partners__badge" role="img" aria-label="Partner badge"></div>
      <div class="partners__mark">
        <span class="partners__dot"></span>
        <span class="partners__name">HOLLAND</span>
      </div>
    </div>
  </section>
</main>
</body>
</html>
```